SaaS Early tech startup business card design

Unique design for experience ecommerce platform company. the business cards will be used by executive members. conformance with color code is required.

```html
<!DOCTYPE html>
<html lang="en">
<head>
<meta charset="utf-8">
<title>Novik business card</title>
<link href="https://fonts.googleapis.com/css2?family=Roboto:wght@400;500;700&display=swap" rel="stylesheet">
<style>
  :root {
    --backdrop: #6c6969;
    --teal-light: #14a093;
    --teal-mid: #12857f;
    --teal-dark: #0e6a6c;
    --navy: #0f4f7b;
    --paper: #f4f5f5;
    --ink: #2b2b2b;
    --white: #ffffff;
  }
  * { margin: 0; padding: 0; box-sizing: border-box; }
  html, body {
    width: 1200px; height: 1200px; overflow: hidden;
    background: var(--backdrop);
    font-family: "Roboto", Arial, sans-serif;
  }
  .card {
    position: absolute; left: 300px; width: 594px; height: 348px;
    border-radius: 22px; overflow: hidden;
  }
  .card svg.bg { position: absolute; inset: 0; width: 100%; height: 100%; }

  /* Front */
  .card-front { top: 199px; background: var(--teal-mid); }
  .front-brand {
    position: absolute; left: 0; right: 0; top: 108px; text-align: center;
    color: var(--white);
  }
  .front-brand .wordmark {
    font-size: 96px; font-weight: 700; line-height: 1; letter-spacing: 1px;
  }
  .front-brand .tagline {
    margin-top: 4px; font-size: 16px; font-weight: 500; letter-spacing: 6px;
    padding-left: 6px;
  }

  /* Back */
  .card-back { top: 637px; background: var(--paper); }
  .back-brand { position: absolute; left: 40px; top: 30px; }
  .back-brand .wordmark {
    font-size: 84px; font-weight: 700; line-height: 1; color: var(--navy); letter-spacing: 1px;
  }
  .back-brand .tagline {
    margin-top: 6px; margin-left: 12px; font-size: 12.5px; font-weight: 500;
    letter-spacing: 5px; color: var(--teal-light);
  }
  .contact { position: absolute; left: 36px; top: 177px; color: var(--ink); font-size: 15px; }
  .contact .address { margin-bottom: 10px; }
  .contact .row { display: flex; align-items: center; gap: 8px; height: 22px; }
  .contact .item { display: flex; align-items: center; gap: 10px; margin-right: 14px; }
  .contact svg { width: 14px; height: 14px; fill: var(--navy); }
  .holder {
    position: absolute; right: 56px; top: 268px; text-align: right; color: var(--white);
  }
  .holder .name { font-size: 24px; font-weight: 700; letter-spacing: -0.3px; }
  .holder .role { font-size: 15px; margin-top: 3px; }
</style>
</head>
<body>

<section class="card card-front" aria-label="Card front">
  <svg class="bg" viewBox="0 0 594 348" preserveAspectRatio="none" aria-hidden="true">
    <defs>
      <linearGradient id="frontShade" x1="0" y1="1" x2="1" y2="0">
        <stop offset="0" stop-color="#15a295"/>
        <stop offset="1" stop-color="#0d6466"/>
      </linearGradient>
    </defs>
    <rect width="594" height="348" fill="#17958b"/>
    <path d="M0 48 C120 10 230 30 330 70 C430 110 520 120 560 80 C580 58 590 30 594 0 L594 348 L0 348 Z" fill="#118079"/>
    <path d="M0 200 C60 160 120 140 170 140 C230 140 280 190 330 240 C390 290 480 300 594 320 L594 348 L0 348 Z" fill="#15a295" opacity="0.9"/>
    <path d="M330 70 C430 110 520 120 560 80 C580 58 590 30 594 0 L594 348 L594 320 C480 300 390 290 330 240 C300 210 280 170 240 145 C280 120 300 80 330 70 Z" fill="url(#frontShade)" opacity="0.55"/>
  </svg>
  <div class="front-brand">
    <div class="wordmark">novik</div>
    <div class="tagline">BUILT AROUND YOU</div>
  </div>
</section>

<section class="card card-back" aria-label="Card back">
  <svg class="bg" viewBox="0 0 594 348" preserveAspectRatio="none" aria-hidden="true">
    <path d="M0 280 C90 320 200 330 300 300 C400 270 470 230 594 232 L594 348 L0 348 Z" fill="var(--navy)"/>
    <path d="M0 262 C60 300 150 310 260 300 C380 288 440 222 594 218 L594 226 C460 226 400 290 280 310 C160 326 70 316 0 292 Z" fill="var(--teal-light)"/>
    <path d="M48 288 C120 306 220 310 300 298 C240 318 130 318 48 288 Z" fill="var(--teal-light)"/>
  </svg>

  <div class="back-brand">
    <div class="wordmark">novik</div>
    <div class="tagline">BUILT AROUND YOU</div>
  </div>

  <div class="contact">
    <div class="address">Harbor Point, Tech Quarter, Marlow</div>
    <div class="row">
      <span class="item">
        <svg viewBox="0 0 24 24" aria-hidden="true"><path d="M2 5h20v14H2z M2 5l10 8 10-8" fill="none" stroke="var(--navy)" stroke-width="2.4"/></svg>
        info@novik.net
      </span>
      <span class="item">
        <svg viewBox="0 0 24 24" aria-hidden="true"><circle cx="12" cy="12" r="9.5" fill="none" stroke="var(--navy)" stroke-width="2"/><path d="M2.5 12h19M12 2.5c-5 5-5 14 0 19M12 2.5c5 5 5 14 0 19" fill="none" stroke="var(--navy)" stroke-width="1.6"/></svg>
        www.novik.net
      </span>
    </div>
    <div class="row">
      <span class="item">
        <svg viewBox="0 0 24 24" aria-hidden="true"><path d="M6.6 10.8a15 15 0 0 0 6.6 6.6l2.2-2.2c.3-.3.7-.4 1-.2 1.1.4 2.3.6 3.6.6.6 0 1 .4 1 1V20c0 .6-.4 1-1 1C10.6 21 3 13.4 3 4c0-.6.4-1 1-1h3.5c.6 0 1 .4 1 1 0 1.3.2 2.5.6 3.6.1.3 0 .7-.2 1z"/></svg>
        (00) 0111 NOVK
      </span>
    </div>
  </div>

  <div class="holder">
    <div class="name">Darin K.</div>
    <div class="role">CTO/Owner</div>
  </div>
</section>

</body>
</html>
```